Existing Website Requiring new Pages

I have an existing word press website that was built using elementor.
Website: www.tallowcrestcare.com.au
I require the Vacancies page (https://www.tallowcrestcare.com.au/vacancies/) to be modified to display our new properties along with minor tweaks to how the information is presented.
The vacancies to be displayed are the exactly the same as those that are located on the homepage of QMR website (https://qmr.org.au/)
The new pages that link off the Vacancies tab will require custom design.
There are roughly 8 pages/properties to be incorporated. i wish for the design to be very similar to that displayed in the following link; https://www.polunda.com.au/vacancies/merrylands
Along with this the back end has not been updated for the last 3 years so it also requires some maintenance.
Website is in the disability industry and the custom pages will display information relative to Property Vacancies.
I have attached a ZIP file with some design guides, the information for each of the properties (which will need to be modified to show our business name Tallowcrest Care) and the example of how it is to look based off the Polunda website.
If you guys have any suggestions or ideas on how to make this more presentable or possible i'm open to your ideas.
Target Market(s)
People looking for SDA properties custom built for people with a disability
Industry/Entity Type
Disability
Coding
Coded - Design and coding required
Number of Pages Required
5+ page

```html
<!DOCTYPE html>
<html lang="en">
<head>
<meta charset="utf-8">
<title>Vacancies | Tallowcrest Care</title>
<link href="https://fonts.googleapis.com/css2?family=Bebas+Neue&family=Montserrat:wght@400;500;600&family=Raleway:wght@400;500;600&display=swap" rel="stylesheet">
<style>
:root{
  --teal:#1ee0bd;
  --pink:#e08ae0;
  --yellow:#fdd785;
  --dark:#3d3d3d;
  --ink:#222;
  --muted:#666;
  --accent:#ec3f7c;
  --orange:#f07d3c;
  --line:#e6e6e6;
  --white:#fff;
}
*{margin:0;padding:0;box-sizing:border-box}
html,body{width:1200px;height:3696px;overflow:hidden;background:var(--white)}
body{position:relative;font-family:'Raleway',sans-serif;color:var(--ink)}
.abs{position:absolute}
.display{font-family:'Bebas Neue',sans-serif;font-weight:400}

/* header */
.site-header{left:0;top:0;width:1200px;height:118px}
.brand{left:136px;top:34px;display:flex;align-items:center;gap:8px}
.brand-dot{width:16px;height:16px;border-radius:50%;background:var(--pink)}
.brand-name{font-family:'Montserrat',sans-serif;font-size:17px;font-weight:500;color:var(--teal);letter-spacing:1px}
.main-nav{top:51px;left:594px;display:flex;gap:28px;font-family:'Montserrat',sans-serif;font-size:10.5px;font-weight:500;color:#555}
.main-nav .current{color:var(--orange)}

/* hero */
.hero-photo{left:560px;top:118px;width:640px;height:433px;background:linear-gradient(135deg,#d9d2c8 0%,#b6a89a 40%,#7d3a36 60%,#cfc8be 100%)}
.hero-panel{left:0;top:118px;width:580px;height:433px;background:var(--teal);border-bottom-right-radius:80px}
.hero-mark{left:180px;top:210px;width:26px;height:44px;background:var(--yellow)}
.hero-title{left:0;top:228px;width:670px;text-align:center;font-family:'Montserrat',sans-serif;font-weight:600;font-size:50px;color:var(--white);letter-spacing:-1px}
.hero-copy{left:135px;top:312px;width:390px;text-align:center;font-size:11px;line-height:15px;color:var(--white)}

/* intro */
.eyebrow{left:0;top:622px;width:1200px;text-align:center;font-family:'Bebas Neue',sans-serif;font-size:13px;color:var(--accent);letter-spacing:.3px}
.section-title{left:0;top:636px;width:1200px;text-align:center;font-size:46px;color:var(--ink)}

/* filter */
.filter-bar{left:307px;top:708px;width:586px;height:72px;background:var(--dark);padding:16px 24px;display:flex;gap:10px;align-items:flex-end}
.filter-field{width:134px}
.filter-field label{display:block;font-family:'Montserrat',sans-serif;font-size:7px;font-weight:600;color:var(--white);margin-bottom:5px}
.filter-select{height:22px;background:var(--white);font-size:9px;color:#999;padding:5px 10px;position:relative}
.filter-select::after{content:"";position:absolute;right:8px;top:8px;border:3px solid transparent;border-top-color:#999}
.filter-go{width:118px;height:22px;background:var(--pink);color:var(--white);font-family:'Montserrat',sans-serif;font-size:9px;font-weight:600;text-align:center;line-height:22px}

/* property cards */
.photo{position:absolute}
.side-bar{position:absolute;width:15px}
.tags{position:absolute;display:flex;gap:5px;font-family:'Montserrat',sans-serif;font-size:12.5px;font-weight:500;color:var(--white)}
.tag{height:30px;line-height:30px;padding:0 12px}
.tag-dark{background:var(--dark)}
.tag-yellow{background:var(--yellow)}
.tag-pink{background:var(--pink)}
.card-text{position:absolute;width:266px;text-align:center;padding:25px 22px 0}
.card-text h3{font-family:'Bebas Neue',sans-serif;font-weight:400;font-size:21px;color:var(--ink);margin-bottom:8px}
.card-text p{font-size:11px;line-height:15px;color:var(--muted);margin-bottom:18px}
.on-colour h3,.on-colour p{color:var(--white)}
.btn{display:inline-block;width:105px;height:31px;line-height:32px;border-radius:16px;background:var(--dark);color:var(--white);font-family:'Bebas Neue',sans-serif;font-size:12px}

/* pagination */
.pager{left:0;top:2660px;width:1200px;display:flex;justify-content:center;align-items:center;gap:10px;font-family:'Montserrat',sans-serif;font-size:11px;letter-spacing:2px;color:var(--ink)}
.pager-btn{width:21px;height:20px;border-radius:3px;display:flex;align-items:center;justify-content:center}

.map-title{left:0;top:2730px;width:1200px;text-align:center;font-size:34px;color:var(--ink)}
.map{left:0;top:2814px;width:1200px;height:536px;background:linear-gradient(160deg,#cfe8c9 0%,#e9ece6 35%,#e8e6e1 65%,#d7e9cd 100%)}

/* footer */
.foot-brand{left:143px;top:3455px;display:flex;align-items:center;gap:8px}
.contact{left:140px;top:3565px;font-family:'Montserrat',sans-serif;font-size:11px;color:#888;line-height:21px}
.contact div{display:flex;align-items:center;gap:8px}
.socials{left:521px;top:3428px;display:flex;flex-direction:column;gap:17px}
.social{width:28px;height:28px;border-radius:50%;background:#1d5fa8}
.social.badge{background:#6a3a95}
.social.black{background:#111}
.foot-col{top:3420px;width:210px}
.foot-col h4{font-family:'Montserrat',sans-serif;font-size:12px;font-weight:500;color:#444;border-left:3px solid #1d7fd1;padding-left:10px;margin-bottom:12px}
.foot-col li{list-style:none;font-family:'Montserrat',sans-serif;font-size:11px;color:#999;line-height:17px;padding:6px 0;border-bottom:1px solid var(--line)}
.copyright{left:0;top:3640px;width:1200px;height:56px;background:#2a2a2a;color:#aaa;font-family:'Montserrat',sans-serif;font-size:9px;text-align:center;line-height:56px}
</style>
</head>
<body>

<header class="site-header abs">
  <div class="brand abs"><span class="brand-dot"></span><span class="brand-name">TALLOWCREST</span></div>
  <nav class="main-nav abs">
    <span>HOME</span><span>ABOUT US</span><span class="current">WHAT WE DO ⌄</span><span>REFERRALS</span><span>FEEDBACK</span><span>CONTACT US</span>
  </nav>
</header>

<section>
  <div class="hero-photo abs" role="img" aria-label="Man in a red shirt working at a laptop at his desk"></div>
  <div class="hero-panel abs"></div>
  <div class="hero-mark abs"></div>
  <h1 class="hero-title abs">VACANCIES</h1>
  <p class="hero-copy abs">In publishing and graphic design, Lorem ipsum is a placeholder text commonly used to demonstrate the visual form In publishing and graphic design, Lorem ipsum is a placeholder text commonly used to demonstrate the visual form of a document or a typeface without relying on meaningful content. In publishing and graphic design, Lorem ipsum is a placeholder text commonly used to demonstrate the visual form of a document or a typeface without relying.</p>
</section>

<p class="eyebrow abs">TALLOWCREST IS A RESIDENT</p>
<h2 class="section-title display abs">CENTRED SDA PROVIDER</h2>

<form class="filter-bar abs">
  <div class="filter-field"><label>CURRENT OR FUTURE</label><div class="filter-select">Both</div></div>
  <div class="filter-field"><label>CURRENT OR FUTURE</label><div class="filter-select">All Categories</div></div>
  <div class="filter-field"><label>CURRENT OR FUTURE</label><div class="filter-select">All Suburbs</div></div>
  <div class="filter-go">GO</div>
</form>

<!-- row 1 -->
<div class="side-bar" style="left:136px;top:940px;height:406px;background:var(--pink)"></div>
<div class="photo" style="left:151px;top:842px;width:428px;height:548px;background:linear-gradient(180deg,#9cc7ea 0%,#e9e4da 45%,#c9b79a 80%,#5f7a45 100%)" role="img" aria-label="Two-storey cream house with balcony"></div>
<div class="tags" style="left:151px;top:858px"><span class="tag tag-yellow">FEATURED</span><span class="tag tag-dark">APPLY NOW</span></div>
<div class="card-text" style="left:151px;top:1202px;height:188px;background:var(--white)">
  <h3>MOUNT DRUITT</h3>
  <p>In publishing and graphic design, Lorem ipsum is a placeholder text commonly used to demonstrate the visual form of a document or a typeface .</p>
  <span class="btn">VIEW DETAILS</span>
</div>

<div class="photo" style="left:586px;top:842px;width:478px;height:548px;background:linear-gradient(180deg,#c9a57e 0%,#b58a63 45%,#9e7a5a 65%,#2aa6c7 85%,#1b7fa6 100%)" role="img" aria-label="Stone villa with terracotta roof beside a swimming pool"></div>
<div class="tags" style="left:586px;top:858px"><span class="tag tag-pink">FEATURED</span><span class="tag tag-dark">APPLY NOW</span></div>
<div class="card-text on-colour" style="left:798px;top:842px;height:188px;background:var(--teal)">
  <h3>SDA IN JORDAN SPRINGS</h3>
  <p>In publishing and graphic design, Lorem ipsum is a placeholder text commonly used to demonstrate the visual form of a document or a typeface .</p>
  <span class="btn">VIEW DETAILS</span>
</div>

<!-- row 2 -->
<div class="photo" style="left:151px;top:1437px;width:428px;height:549px;background:linear-gradient(180deg,#dfe5ea 0%,#b7b2aa 40%,#8a6a55 65%,#5b5b5b 100%)" role="img" aria-label="Brick townhouse with balconies and garage"></div>
<div class="tags" style="left:151px;top:1453px"><span class="tag tag-yellow">FEATURED</span><span class="tag tag-dark">APPLY NOW</span></div>
<div class="card-text" style="left:151px;top:1797px;height:189px;background:var(--yellow)">
  <h3>GUILDFORD WEST</h3>
  <p>In publishing and graphic design, Lorem ipsum is a placeholder text commonly used to demonstrate the visual form of a document or a typeface .</p>
  <span class="btn">VIEW DETAILS</span>
</div>

<div class="side-bar" style="left:1064px;top:1451px;width:12px;height:488px;background:var(--yellow)"></div>
<div class="photo" style="left:586px;top:1437px;width:478px;height:549px;background:linear-gradient(180deg,#f2f1ee 0%,#e6e3dd 50%,#b98a5e 75%,#8f6a48 100%)" role="img" aria-label="Empty living area with timber floor and kitchen"></div>
<div class="tags" style="left:586px;top:1453px"><span class="tag tag-pink">FEATURED</span><span class="tag tag-dark">APPLY NOW</span></div>
<div class="card-text" style="left:798px;top:1437px;height:188px;background:var(--white)">
  <h3>SDA IN BLACKTOWN</h3>
  <p>In publishing and graphic design, Lorem ipsum is a placeholder text commonly used to demonstrate the visual form of a document or a typeface .</p>
  <span class="btn">VIEW DETAILS</span>
</div>

<!-- row 3 -->
<div class="side-bar" style="left:136px;top:2153px;height:405px;background:var(--pink)"></div>
<div class="photo" style="left:151px;top:2054px;width:428px;height:549px;background:linear-gradient(180deg,#2f5fa8 0%,#5b83c0 40%,#c9b8a4 65%,#4f4a44 100%)" role="img" aria-label="Modern two-storey house lit at dusk"></div>
<div class="tags" style="left:151px;top:2070px"><span class="tag tag-yellow">FEATURED</span><span class="tag tag-dark">APPLY NOW</span></div>
<div class="card-text" style="left:151px;top:2415px;height:188px;background:var(--white)">
  <h3>SDA IN MERRYLANDS</h3>
  <p>In publishing and graphic design, Lorem ipsum is a placeholder text commonly used to demonstrate the visual form of a document or a typeface .</p>
  <span class="btn">VIEW DETAILS</span>
</div>

<div class="photo" style="left:586px;top:2054px;width:478px;height:549px;background:linear-gradient(180deg,#3a5e8f 0%,#8a9bb0 35%,#d8cbb5 60%,#2b7fb8 85%,#174f80 100%)" role="img" aria-label="Contemporary white house with pool at dusk"></div>
<div class="tags" style="left:586px;top:2070px"><span class="tag tag-pink">FEATURED</span><span class="tag tag-dark">APPLY NOW</span></div>
<div class="card-text on-colour" style="left:798px;top:2054px;height:189px;background:var(--pink)">
  <h3>SDA IN WEST PENNANT HILLS</h3>
  <p>In publishing and graphic design, Lorem ipsum is a placeholder text commonly used to demonstrate the visual form of a document or a typeface .</p>
  <span class="btn">VIEW DETAILS</span>
</div>

<div class="pager abs">
  <span class="pager-btn" style="background:var(--teal)"><svg width="10" height="10" viewBox="0 0 10 10"><path d="M5 2L2 5l3 3M8 2L5 5l3 3" stroke="#fff" stroke-width="1.4" fill="none"/></svg></span>
  <span>123456789</span>
  <span class="pager-btn" style="background:#888"><svg width="10" height="10" viewBox="0 0 10 10"><path d="M2 2l3 3-3 3M5 2l3 3-3 3" stroke="#fff" stroke-width="1.4" fill="none"/></svg></span>
</div>

<h2 class="map-title display abs">VIEW OUR SDA VACANCIES AND HOMES BEING BUILT</h2>
<div class="map abs" role="img" aria-label="Map of western Sydney suburbs with property location markers"></div>

<footer>
  <div class="foot-brand abs"><span class="brand-dot"></span><span class="brand-name">TALLOWCREST</span></div>
  <div class="contact abs">
    <div><svg width="12" height="10" viewBox="0 0 12 10"><rect x=".7" y=".7" width="10.6" height="8.6" fill="none" stroke="#ec3f7c" stroke-width="1.2"/><path d="M1 1l5 4 5-4" stroke="#ec3f7c" stroke-width="1.2" fill="none"/></svg>Email: info@tallowcrestcare.com.au</div>
    <div><svg width="12" height="12" viewBox="0 0 12 12"><path d="M2 1l2.5 0 1 3-1.5 1c.8 1.6 1.8 2.6 3.2 3.2l1-1.5 3 1V10.5c0 .5-.5 1-1 1C5 11 1 7 1 2c0-.5.5-1 1-1z" fill="#ec3f7c"/></svg>Phone: +61 0400 318 562</div>
    <div><svg width="12" height="12" viewBox="0 0 12 12"><circle cx="6" cy="6" r="5" fill="none" stroke="#ec3f7c" stroke-width="1.2"/><path d="M6 3v3l2 1.5" stroke="#ec3f7c" stroke-width="1.2" fill="none"/></svg>Operating Hours: 9AM To 5PM Monday - Friday</div>
  </div>
  <div class="socials abs">
    <span class="social badge"></span><span class="social"></span><span class="social black"></span><span class="social"></span>
  </div>
  <div class="foot-col abs" style="left:606px">
    <h4>ACCOMMODATION</h4>
    <ul>
      <li>Supported Independent Living (SIL)</li>
      <li>Specialist Disability Accommodation (SDA)</li>
      <li>Short term Accommodation (Respite)</li>
      <li>Vacancies</li>
    </ul>
  </div>
  <div class="foot-col abs" style="left:838px">
    <h4>WHAT WE DO</h4>
    <ul>
      <li>In Home Care</li>
      <li>Social &amp; Community Services</li>
      <li>Therapeutic Supports</li>
      <li>Support Coordination</li>
      <li>Home Modifications</li>
    </ul>
  </div>
  <div class="copyright abs">© Copyright 2021 | Tallowcrest Care | All Rights Reserved.</div>
</footer>

</body>
</html>
```